5KO Outings

Explain what 5KO means ( Water, Wave, Wake Expereince)
We offer surfing, wake baording, water skliing on a state of the art surf and equipment all included in the charter. The captain is a Norvane Shore Watch captain.
We offer wake surfing, wakeboarding, water skiing, tubing. We have state of the art video with 3 cameras onboard 2,360 view camers for videioing your day on the water.
Located on the Delta, serving Lake Tahoe in the summer time, Lake Berryasea, and other local lakes.
We specliaize in birthday parties, bacholer, bachlorrete, graduation parties and team building events.

Target Market(s)

Indivuals, business, wedding and event planners

Industry/Entity Type

Water sports

Requirements
Must have
• My logo,
Nice to have
• Simple, not to busy

```html
<!DOCTYPE html>
<html lang="en">
<head>
<meta charset="utf-8">
<title>5KO Outings – Flyer</title>
<link href="https://fonts.googleapis.com/css2?family=Montserrat:wght@500;700;800&family=Oswald:wght@500;600;700&display=swap" rel="stylesheet">
<style>
  :root{
    --page:#e9ecee;
    --sea-deep:#16aac0;
    --sea:#2cc0d2;
    --foam:#eef8fb;
    --ink:#1b8fa1;
    --panel:rgba(233,246,250,0.9);
    --white:#ffffff;
  }
  *{margin:0;padding:0;box-sizing:border-box;}
  html,body{width:960px;height:1200px;overflow:hidden;background:var(--page);}
  .flyer{
    position:absolute;left:60px;top:6px;width:840px;height:1188px;overflow:hidden;
    font-family:'Montserrat',sans-serif;color:var(--ink);
  }
  .hero-photo{
    position:absolute;inset:0;
    background:linear-gradient(170deg, var(--sea) 0%, var(--sea-deep) 60%, #22b7c9 100%);
  }
  .brand{
    position:absolute;top:70px;left:0;width:100%;
    display:flex;justify-content:center;align-items:center;gap:10px;
    color:var(--white);font-weight:700;font-size:30px;letter-spacing:1px;
  }
  .brand-dot{width:18px;height:18px;border-radius:50%;background:var(--white);}
  .tagline{
    position:absolute;top:145px;width:100%;text-align:center;
    color:var(--white);font-weight:700;font-size:13.5px;letter-spacing:.6px;
  }
  .headline{
    position:absolute;top:432px;width:100%;text-align:center;
    font-family:'Oswald',sans-serif;font-weight:700;font-size:172px;line-height:1;
    letter-spacing:8px;
    background:linear-gradient(180deg,#f2f8fb 0%,#d9eef4 55%,#9fd9e4 100%);
    -webkit-background-clip:text;background-clip:text;color:transparent;
  }
  .headline-sub{
    position:absolute;top:612px;width:100%;text-align:center;line-height:1.2;
    font-family:'Oswald',sans-serif;font-weight:500;font-size:25px;color:var(--foam);
  }
  .offer-banner{
    position:absolute;left:271px;top:877px;width:302px;height:40px;
  }
  .offer-banner svg{position:absolute;inset:0;}
  .offer-banner span{
    position:relative;display:block;text-align:center;line-height:40px;
    font-weight:800;font-size:20px;color:var(--ink);
  }
  .offer-panel{
    position:absolute;left:36px;top:935px;width:776px;height:223px;
    background:var(--panel);border-radius:14px;
  }
  .activities{
    position:absolute;top:9px;width:100%;
    display:flex;justify-content:center;gap:22px;
    font-family:'Oswald',sans-serif;font-weight:500;font-size:30px;line-height:40px;color:var(--ink);
  }
  .intro{
    position:absolute;top:58px;width:100%;text-align:center;
    font-weight:500;font-size:18px;line-height:22px;
  }
  .video-note{
    position:absolute;left:40px;top:117px;width:330px;
    font-weight:500;font-size:15px;line-height:19px;
  }
  .location{
    position:absolute;left:377px;top:117px;width:390px;display:flex;gap:18px;
    font-weight:500;font-size:15px;line-height:19px;
  }
  .location svg{flex:none;margin-top:6px;}
  .specialties{
    position:absolute;top:195px;width:100%;text-align:center;
    font-weight:700;font-size:11.6px;
  }
  b{font-weight:700;}
</style>
</head>
<body>
  <main class="flyer">
    <div class="hero-photo" role="img" aria-label="Aerial photo of a jet ski on turquoise water"></div>

    <div class="brand"><span class="brand-dot"></span>5KO OUTINGS</div>
    <p class="tagline">SURF IT, LAUNCH IT, CARVE IT!</p>

    <h1 class="headline">5KO</h1>
    <p class="headline-sub">WATER, WAVE, WAKE EXPEREINCE</p>

    <div class="offer-banner">
      <svg width="302" height="40" viewBox="0 0 302 40">
        <path d="M10 4 H292 L300 10 L294 17 L301 23 L294 30 L298 36 L10 36 L2 30 L8 23 L1 17 L8 10 Z" fill="#e9f6fa"/>
      </svg>
      <span>WHAT WE OFFER</span>
    </div>

    <section class="offer-panel">
      <h2 class="activities"><span>WAKE SURFING,</span><span>WAKEBOARDING,</span><span>WATER SKIING,</span><span>TUBING</span></h2>
      <p class="intro">All on a state of the art surf and equipment all included in the charter.<br>The captain is a <b>Norvane Shore Watch</b> captain.</p>
      <p class="video-note">We have state of the artvideo with 3<br>cameras onboard 2, <b>360 view</b> camers<br>for <b>videioing</b> your day on the water.</p>
      <div class="location">
        <svg width="30" height="40" viewBox="0 0 26 34" aria-hidden="true">
          <path d="M13 1C6.4 1 1 6.2 1 12.8 1 21.5 13 33 13 33S25 21.5 25 12.8C25 6.2 19.6 1 13 1Z" fill="var(--ink)"/>
          <circle cx="13" cy="12.5" r="4.6" fill="#e9f6fa"/>
        </svg>
        <p>Located on the <b>Delta</b>, serving<br><b>Lake Tahoe</b> in the summer time,<br><b>Lake Berryasea</b>, and other local lakes.</p>
      </div>
      <p class="specialties">WE SPECLIAIZE IN BIRTHDAY PARTIES, BACHOLER, BACHLORRETE, GRADUATION PARTIES AND TEAM BUILDING EVENTS.</p>
    </section>
  </main>
</body>
</html>
```